Business Card Design

We need a business card designed for our new company. Prefer a black card with white logo & writing.

Contact Information for Business Card

Ted Galloway, address: 7-4812 Fernhollow Road, Abbotsford, BC, V3K 8R2, Office Phone: 604-712-3390, Cell: 604-947-2164, Email: ted@resinworkshub.ca

Colors

Designer to choose only greyscale colors for use in the design.

```html
<!DOCTYPE html>
<html lang="en">
<head>
<meta charset="UTF-8">
<title>Resin Works Hub — Business Card</title>
<link href="https://fonts.googleapis.com/css2?family=Montserrat:wght@400;600;700;800&display=swap" rel="stylesheet">
<style>
  :root {
    --backdrop: #e4e4e4;
    --card: #1f1f1f;
    --ink: #ffffff;
    --ink-soft: #e6e6e6;
    --ink-muted: #cfcfcf;
  }
  * { margin: 0; padding: 0; box-sizing: border-box; }
  html, body { width: 900px; height: 1200px; overflow: hidden; }
  body {
    position: relative;
    background: var(--backdrop);
    font-family: "Montserrat", sans-serif;
    color: var(--ink);
  }
  .card {
    position: absolute;
    left: 80px;
    width: 742px;
    height: 442px;
    background: var(--card);
    border-radius: 22px;
  }
  .card--front { top: 130px; }
  .card--back { top: 636px; }

  .brand-name {
    position: absolute;
    left: 0; right: 0;
    text-align: center;
    font-weight: 800;
    color: var(--ink);
    letter-spacing: 0.5px;
    white-space: nowrap;
  }
  .card--front .brand-name { top: 92px; font-size: 42px; }
  .card--back .brand-name { top: 200px; font-size: 56px; }

  .person {
    position: absolute;
    right: 398px;
    top: 278px;
    text-align: right;
  }
  .person__name { font-size: 24px; font-weight: 700; line-height: 1; }
  .person__role { margin-top: 12px; font-size: 15px; color: var(--ink-muted); }

  .divider {
    position: absolute;
    left: 371px;
    top: 258px;
    width: 2px;
    height: 100px;
    background: var(--ink);
  }

  .contacts {
    position: absolute;
    left: 394px;
    top: 255px;
    list-style: none;
  }
  .contacts li {
    display: flex;
    align-items: center;
    height: 27px;
    font-size: 15px;
    color: var(--ink-soft);
  }
  .contacts svg { width: 16px; height: 16px; margin-right: 12px; fill: var(--ink); flex: none; }

  .address {
    position: absolute;
    left: 0; right: 0;
    top: 390px;
    text-align: center;
    font-size: 16px;
    color: var(--ink-soft);
  }
</style>
</head>
<body>
  <section class="card card--front">
    <div class="brand-name">Resin Works Hub</div>

    <div class="person">
      <div class="person__name">Ted Galloway</div>
      <div class="person__role">owner</div>
    </div>

    <div class="divider"></div>

    <ul class="contacts">
      <li>
        <svg viewBox="0 0 24 24" aria-hidden="true"><path d="M6.6 10.8a15.1 15.1 0 0 0 6.6 6.6l2.2-2.2a1 1 0 0 1 1-.25 11.4 11.4 0 0 0 3.6.57 1 1 0 0 1 1 1V20a1 1 0 0 1-1 1A17 17 0 0 1 3 4a1 1 0 0 1 1-1h3.5a1 1 0 0 1 1 1c0 1.25.2 2.45.57 3.57a1 1 0 0 1-.25 1z"/></svg>
        604-712-3390
      </li>
      <li>
        <svg viewBox="0 0 24 24" aria-hidden="true"><path d="M7 2h10a2 2 0 0 1 2 2v16a2 2 0 0 1-2 2H7a2 2 0 0 1-2-2V4a2 2 0 0 1 2-2zm0 3v13h10V5zm5 14.2a1 1 0 1 0 0 .01z"/></svg>
        604-947-2164
      </li>
      <li>
        <svg viewBox="0 0 24 24" aria-hidden="true"><path d="M3 5h18v14H3zm2 2v.5l7 4.5 7-4.5V7z"/></svg>
        ted@resinworkshub.ca
      </li>
      <li>
        <svg viewBox="0 0 24 24" aria-hidden="true"><path d="M12 2a10 10 0 1 0 0 20 10 10 0 0 0 0-20zm6.9 9h-3a15 15 0 0 0-1.3-6A8 8 0 0 1 18.9 11zM12 4.1A13 13 0 0 1 13.9 11h-3.8A13 13 0 0 1 12 4.1zM9.4 5a15 15 0 0 0-1.3 6h-3A8 8 0 0 1 9.4 5zM5.1 13h3a15 15 0 0 0 1.3 6 8 8 0 0 1-4.3-6zm6.9 6.9A13 13 0 0 1 10.1 13h3.8A13 13 0 0 1 12 19.9zm2.6-.9a15 15 0 0 0 1.3-6h3a8 8 0 0 1-4.3 6z"/></svg>
        www.resinworkshub.ca
      </li>
    </ul>

    <div class="address">7-4812 Fernhollow Road, Abbotsford, BC, V3K 8R2</div>
  </section>

  <section class="card card--back">
    <div class="brand-name">Resin Works Hub</div>
  </section>
</body>
</html>
```